BLS Business Card 2018

Larkmere Chiropractic. We have two locations that we want to advertise on the same card. Brightvale OrthoCore campus address: 3815 Pellham Dr., Suite 240, Flowood, MS 39417. Madison address: 246 Willowmere Dr., Building D., Madison, MS 39284. website: www.drlarkmere-example.com. o:(601)555-0147 f:(601)555-0183

Target Market(s)

Health care decision makers: primary care doctors and mothers

Contact Information for Business Card

I have no idea; up for any suggestions and I'd do much better picking from examples versus describing what I'm looking for. We are in a very high end location and would like the cards to look really sharp.

Requirements
Must have
• My name, Martin R Belvane, D.C.

```html
<!DOCTYPE html>
<html lang="en">
<head>
<meta charset="utf-8">
<title>Larkmere Chiropractic – Business Card</title>
<link rel="stylesheet" href="https://fonts.googleapis.com/css2?family=Cinzel:wght@400&family=Roboto:wght@400&family=Roboto+Condensed:wght@700&display=swap">
<style>
  :root {
    --backdrop: #e9e6e1;
    --card-light: #ffffff;
    --card-dark: #1b1c1e;
    --ink: #111111;
    --ink-soft: #555555;
    --ink-inverse: #ffffff;
  }
  * { margin: 0; padding: 0; box-sizing: border-box; }
  html, body {
    width: 1200px;
    height: 960px;
    overflow: hidden;
    background: var(--backdrop);
  }
  .canvas {
    position: relative;
    width: 1200px;
    height: 960px;
  }
  .card {
    position: absolute;
    width: 600px;
    height: 342px;
    overflow: hidden;
  }
  .card--front {
    left: 314px;
    top: 113px;
    background: var(--card-light);
  }
  .card--back {
    left: 312px;
    top: 472px;
    height: 343px;
    background: var(--card-dark);
  }
  .wordmark {
    position: absolute;
    font-family: "Cinzel", serif;
    font-weight: 400;
    line-height: 1;
    white-space: nowrap;
  }
  .wordmark span { display: block; }
  .card--front .wordmark {
    left: 106px;
    top: 52px;
    color: var(--ink);
    font-size: 30px;
  }
  .card--front .wordmark .wordmark__sub { font-size: 20px; margin-top: 2px; }
  .card--back .wordmark {
    left: 208px;
    top: 128px;
    color: var(--ink-inverse);
    font-size: 42px;
  }
  .card--back .wordmark .wordmark__sub { font-size: 28px; margin-top: 3px; }
  .contact {
    position: absolute;
    left: 34px;
    font-family: "Roboto", sans-serif;
    font-size: 14.5px;
    line-height: 18.3px;
    color: var(--ink-soft);
    font-style: normal;
  }
  .contact--addresses { top: 149px; }
  .contact--lines { top: 267px; }
  .holder-name {
    position: absolute;
    right: 33px;
    top: 255px;
    font-family: "Roboto Condensed", sans-serif;
    font-weight: 700;
    font-size: 21px;
    color: var(--ink);
    white-space: nowrap;
  }
  .edge-dot {
    position: absolute;
    left: 577px;
    top: 251px;
    width: 38px;
    height: 38px;
    border-radius: 50%;
    background: var(--ink);
  }
  .website {
    position: absolute;
    left: 0;
    right: 0;
    top: 282px;
    text-align: center;
    font-family: "Roboto", sans-serif;
    font-size: 14px;
    letter-spacing: 4.5px;
    color: var(--ink-inverse);
    text-transform: uppercase;
  }
</style>
</head>
<body>
<main class="canvas">
  <section class="card card--front">
    <div class="wordmark">
      <span class="wordmark__main">Larkmere</span>
      <span class="wordmark__sub">Chiropractic</span>
    </div>
    <address class="contact contact--addresses">
      Brightvale OrthoCore campus :<br>
      3815 Pellham Dr., Suite 240<br>
      Flowood, MS 39417.<br>
      Madison address:<br>
      246 Willowmere Dr., Building D.<br>
      Madison, MS 39284.
    </address>
    <p class="contact contact--lines">
      Phone : (601)555-0147<br>
      Fax : (601)555-0183
    </p>
    <p class="holder-name">MARTIN R BELVANE, D.C.</p>
    <div class="edge-dot"></div>
  </section>

  <section class="card card--back">
    <div class="wordmark">
      <span class="wordmark__main">Larkmere</span>
      <span class="wordmark__sub">Chiropractic</span>
    </div>
    <p class="website">www.drlarkmere-example.com</p>
  </section>
</main>
</body>
</html>
```